Home Remodeling company needs a business card design

we need a business card design for home remodeling company in hamilton county, indiana USA. we offers a wide range of construction services including whole house renovations, Design and Build Basements and Kitchen and Bathroom Remodeling . we would like to see designs for both site of business card that use the same color of the company logo and also including all information below :
1- Karim Feltous CEO / General Contractor
2- all company contacts Telephone numbers ( 1-888-DULOM-47 ) ( 317-555-0193) email address ( info@dulomhome.com) website ( www.dulomhome.com ) and social media logos (Facebook- twitter- google plus )
3- company logo
4- licensed . insured . bonded

```html
<!DOCTYPE html>
<html lang="en">
<head>
<meta charset="utf-8">
<title>Dulom Home Remodeling – Business Card</title>
<link rel="stylesheet" href="https://fonts.googleapis.com/css2?family=Cabin:wght@400;600&display=swap">
<style>
  :root {
    --backdrop: #9b9b9b;
    --card-white: #f1f1f0;
    --ink: #3a3a3c;
    --ink-soft: #2e2e30;
    --brand-red: #a92a33;
    --on-red: #f4f1f1;
  }
  * { box-sizing: border-box; margin: 0; padding: 0; }
  html, body {
    width: 1105px; height: 1200px; overflow: hidden;
    background: var(--backdrop);
    font-family: "Cabin", "Gill Sans", sans-serif;
  }
  .canvas { position: relative; width: 1105px; height: 1200px; }
  .card {
    position: absolute; left: 180px;
    width: 746px; height: 425px; overflow: hidden;
  }
  .card--front { top: 120px; background: var(--card-white); }
  .card--back { top: 637px; background: var(--brand-red); }

  /* company name: one colour, one weight, one plain square */
  .company { position: absolute; display: flex; align-items: center; gap: 14px; white-space: nowrap; }
  .company__square { width: 16px; height: 16px; flex: none; }
  .company__name { font-weight: 600; font-size: 32px; letter-spacing: 1.5px; line-height: 1; }

  .card--front .company { left: 46px; top: 72px; }
  .card--front .company__square { background: var(--brand-red); }
  .card--front .company__name { color: var(--ink); }

  .card--back .company { left: 50%; top: 186px; transform: translateX(-50%); }
  .card--back .company__square { background: var(--on-red); }
  .card--back .company__name { color: var(--on-red); }

  /* contacts */
  .contacts { position: absolute; left: 46px; top: 262px; list-style: none; }
  .contacts__item {
    display: flex; align-items: center; gap: 12px;
    height: 29px; font-size: 19px; color: var(--ink-soft); white-space: nowrap;
  }
  .contacts__icon { width: 16px; height: 16px; fill: var(--ink-soft); flex: none; }

  /* name plate */
  .nameplate { position: absolute; left: 408px; top: 283px; width: 338px; height: 66px; }
  .nameplate__band { position: absolute; inset: 0; width: 100%; height: 100%; }
  .nameplate__text {
    position: absolute; right: 30px; top: 6px; text-align: right; color: #fff; white-space: nowrap;
  }
  .nameplate__name { font-size: 26px; font-weight: 400; letter-spacing: 0.5px; line-height: 1.15; }
  .nameplate__title { font-size: 19px; line-height: 1.2; }

  /* credentials */
  .credentials {
    position: absolute; left: 0; right: 0; top: 250px; text-align: center;
    font-size: 15px; letter-spacing: 3px; color: var(--on-red);
  }

  /* social row */
  .social { position: absolute; left: 0; right: 0; top: 360px; display: flex; justify-content: center; align-items: center; gap: 6px; }
  .social__rule { width: 62px; height: 1px; background: rgba(244,241,241,0.6); }
  .social__dot { width: 25px; height: 25px; border-radius: 50%; background: var(--on-red); }
</style>
</head>
<body>
<main class="canvas">

  <section class="card card--front" aria-label="Card front">
    <div class="company">
      <span class="company__square"></span>
      <span class="company__name">DULOM HOME REMODELING</span>
    </div>

    <ul class="contacts">
      <li class="contacts__item">
        <svg class="contacts__icon" viewBox="0 0 16 16" aria-hidden="true"><path d="M3.2 1l2.6 2.8-1.4 2c.9 1.9 2.4 3.4 4.3 4.3l2-1.4L13.5 11.3 12 14.5C6.2 14 1.9 9.7 1.5 4z"/></svg>
        1-888-DULOM-47
      </li>
      <li class="contacts__item">
        <svg class="contacts__icon" viewBox="0 0 16 16" aria-hidden="true"><path d="M4 0h8a1 1 0 0 1 1 1v14a1 1 0 0 1-1 1H4a1 1 0 0 1-1-1V1a1 1 0 0 1 1-1zm.6 2v10.5h6.8V2zM8 13.2a.9.9 0 1 0 0 1.8.9.9 0 0 0 0-1.8z"/></svg>
        317-555-0193
      </li>
      <li class="contacts__item">
        <svg class="contacts__icon" viewBox="0 0 16 16" aria-hidden="true"><path d="M1 3.5h14v9H1zm1.3 1.1L8 9l5.7-4.4z"/></svg>
        info@dulomhome.com
      </li>
      <li class="contacts__item">
        <svg class="contacts__icon" viewBox="0 0 16 16" aria-hidden="true"><path d="M8 1a7 7 0 1 0 0 14A7 7 0 0 0 8 1zm-1 2.2c-.6 1-1.8 1.4-2 2.6.5 1 1.8.6 2.3 1.6-.3 1.2.6 1.8.4 3.4C6.3 11 5 9.6 4 8.4 3.6 6 5 3.9 7 3.2zm2.3.1c2 .6 3.5 2.5 3.5 4.7 0 1-.3 2-.9 2.8-.6-.7-.4-2-1.4-2.5-.9-.1-1.6-.8-1.3-1.8.5-.6 1.2-1 1-2-.4-.5-.8-.8-.9-1.2z"/></svg>
        www.dulomhome.com
      </li>
    </ul>

    <div class="nameplate">
      <svg class="nameplate__band" viewBox="0 0 338 66" preserveAspectRatio="none" aria-hidden="true">
        <polygon points="40,0 323,0 323,66 0,66" fill="var(--ink-soft)"/>
        <rect x="327" y="0" width="11" height="66" fill="var(--brand-red)"/>
      </svg>
      <div class="nameplate__text">
        <p class="nameplate__name">Karim Feltous</p>
        <p class="nameplate__title">CEO / General Contractor</p>
      </div>
    </div>
  </section>

  <section class="card card--back" aria-label="Card back">
    <div class="company">
      <span class="company__square"></span>
      <span class="company__name">DULOM HOME REMODELING</span>
    </div>

    <p class="credentials">LICENSED . INSURED . BONDED</p>

    <div class="social" aria-label="Social media links">
      <span class="social__rule"></span>
      <span class="social__dot"></span>
      <span class="social__dot"></span>
      <span class="social__dot"></span>
      <span class="social__rule"></span>
    </div>
  </section>

</main>
</body>
</html>
```